Verodex business card

Business card for sustainable investment company called "Verodex". Verodex is an exchange platform selling carbon credits between buyers and sellers. Carbon Credits are an environmental commodity for reducing global carbon emissions.

the card should obviously have our logo and the theme should be sustainability/environment mixed with a trading platform.

Contact Information for Business Card

Logo, Name, Title, Phone, Email

Colors
0054AA
0677BA
7BADD7
CADEEF
E8F1F8
0094D4
00A9DD
6FCCEA
C7EBF8
E9F6FB
00AB8E
00BBA5
67D7C9
C6EFE9
E9F9F6
59FF00
82FF00
B8FF75
E3FFCB
F4FFEA

```html
<!DOCTYPE html>
<html lang="en">
<head>
<meta charset="utf-8">
<title>Verodex business card</title>
<link rel="stylesheet" href="https://fonts.googleapis.com/css2?family=Montserrat:wght@400;500;600;700&display=swap">
<style>
  :root {
    --stage: #2a2a2a;
    --navy: #23344f;
    --white: #ffffff;
    --cyan: #2ec8ef;
    --blue: #2174e8;
    --ink: #1f2f4a;
    --rule: #b9b9b9;
  }
  * { box-sizing: border-box; margin: 0; padding: 0; }
  html, body { width: 1200px; height: 689px; overflow: hidden; }
  body {
    background: var(--stage);
    font-family: "Montserrat", sans-serif;
    position: relative;
  }
  .card {
    position: absolute;
    top: 190px;
    width: 540px;
    height: 309px;
    border-radius: 22px;
    overflow: hidden;
  }
  /* Front */
  .card-front { left: 40px; background: var(--navy); }
  .front-mark {
    position: absolute;
    left: 0; top: 0;
    width: 210px; height: 100%;
    background: linear-gradient(135deg, var(--cyan), var(--blue));
  }
  .front-name {
    position: absolute;
    left: 250px; top: 50%;
    transform: translateY(-50%);
    color: var(--white);
    font-weight: 700;
    font-size: 44px;
    letter-spacing: 1px;
  }
  /* Back */
  .card-back { left: 620px; background: var(--white); }
  .back-brand {
    position: absolute;
    left: 34px; top: 110px;
    display: flex; align-items: center; gap: 12px;
  }
  .back-brand-square {
    width: 28px; height: 28px;
    border-radius: 4px;
    background: linear-gradient(135deg, var(--cyan), var(--blue));
  }
  .back-brand-name {
    color: var(--ink);
    font-weight: 700;
    font-size: 28px;
    letter-spacing: 0.5px;
  }
  .divider {
    position: absolute;
    left: 262px; top: 40px;
    width: 1px; height: 170px;
    background: linear-gradient(to bottom, transparent, var(--rule), transparent);
  }
  .contact { position: absolute; left: 286px; top: 52px; color: var(--ink); }
  .contact-name { font-weight: 700; font-size: 20px; letter-spacing: 0.5px; }
  .contact-title { font-weight: 500; font-size: 13px; margin-top: 2px; }
  .contact-list { list-style: none; margin-top: 22px; }
  .contact-list li {
    display: flex; align-items: center; gap: 8px;
    font-size: 12.5px; font-weight: 500;
    margin-bottom: 6px;
  }
  .contact-list svg { width: 13px; height: 13px; flex: none; }
  .band {
    position: absolute;
    left: 0; bottom: 0;
    width: 100%; height: 62px;
    background: var(--navy);
    border-top: 5px solid var(--white);
    box-shadow: 0 -3px 0 0 var(--blue);
  }
  .band::before {
    content: "";
    position: absolute; left: 0; top: -8px;
    width: 100%; height: 3px;
    background: linear-gradient(90deg, var(--blue), var(--cyan), var(--blue));
  }
  .band-name {
    position: absolute;
    right: 26px; top: 50%;
    transform: translateY(-50%);
    color: var(--white);
    font-weight: 700; font-size: 15px;
    letter-spacing: 0.5px;
  }
</style>
</head>
<body>
  <section class="card card-front">
    <div class="front-mark"></div>
    <div class="front-name">VERODEX</div>
  </section>

  <section class="card card-back">
    <div class="back-brand">
      <span class="back-brand-square"></span>
      <span class="back-brand-name">VERODEX</span>
    </div>
    <div class="divider"></div>
    <div class="contact">
      <div class="contact-name">DANIEL WHITFORD</div>
      <div class="contact-title">Managing Director</div>
      <ul class="contact-list">
        <li>
          <svg viewBox="0 0 16 16" aria-hidden="true"><path fill="#1f2f4a" d="M3.6 1.5l2.3 2.3-1.3 1.9a9 9 0 0 0 5.7 5.7l1.9-1.3 2.3 2.3-1.6 2.1C7.4 14.3 1.7 8.6 1.5 3.1z"/></svg>
          044-555 019 284
        </li>
        <li>
          <svg viewBox="0 0 16 16" aria-hidden="true"><rect x="1" y="3" width="14" height="10" fill="#1f2f4a"/><path d="M1.5 3.5 8 9l6.5-5.5" stroke="#fff" stroke-width="1.4" fill="none"/></svg>
          hello@verodexmail.com
        </li>
        <li>
          <svg viewBox="0 0 16 16" aria-hidden="true"><g fill="none" stroke="#1f2f4a" stroke-width="1.3"><circle cx="8" cy="8" r="6.5"/><ellipse cx="8" cy="8" rx="2.8" ry="6.5"/><path d="M1.5 8h13M2.5 4.8h11M2.5 11.2h11"/></g></svg>
          www.verodexexchange.com
        </li>
      </ul>
    </div>
    <div class="band"><span class="band-name">VERODEX</span></div>
  </section>
</body>
</html>
```